Dorwin and Partners Outpatient Imaging

1. flyer/rack card size, front and back for imaging services advertisement. Color design. Text file and one chest xray and one hand radiograph hopefully. Clean and easy to read. 2. clear to read title about "Outpatient imaging services" 3. Only using images and text provided. This is a radiology group offering web based image interpretation to physicians in the community.

Target Market(s)

Referring outpatient physicians

Industry/Entity Type

Medical Imaging

Font styles to use
Serif

Requirements
Must have
• preferably one picture, easy to read design
Nice to have
• both a hand and chest xray would be nice.

```html
<!DOCTYPE html>
<html lang="en">
<head>
<meta charset="utf-8">
<title>Dorwin and Partners Outpatient Imaging</title>
<link href="https://fonts.googleapis.com/css2?family=Lato:wght@400;700;900&display=swap" rel="stylesheet">
<style>
  :root {
    --brand-red: #a81e2b;
    --band-red: #a31f29;
    --ink: #231f20;
    --paper: #ffffff;
  }
  html, body {
    margin: 0;
    padding: 0;
    width: 1200px;
    height: 2557px;
    overflow: hidden;
    background: var(--paper);
  }
  .rack-card {
    position: relative;
    width: 1200px;
    height: 2557px;
    background: var(--paper);
    font-family: "Lato", Arial, sans-serif;
    color: var(--ink);
  }
  .body-copy {
    position: absolute;
    left: 80px;
    width: 1040px;
    margin: 0;
    font-size: 33px;
    line-height: 44.7px;
    text-align: justify;
    text-align-last: left;
  }
  .intro { top: 160px; }
  .services-copy { top: 680px; }
  .section-title {
    position: absolute;
    left: 78px;
    top: 585px;
    margin: 0;
    font-size: 63px;
    font-weight: 900;
    color: var(--brand-red);
    letter-spacing: 0.2px;
    line-height: 1;
  }
  .callout {
    position: absolute;
    left: 0;
    width: 1200px;
    top: 1366px;
    margin: 0;
    text-align: center;
    font-size: 54px;
    line-height: 71px;
    font-weight: 900;
    color: var(--brand-red);
  }
  .contact {
    position: absolute;
    left: 0;
    width: 1200px;
    top: 1683px;
    margin: 0;
    text-align: center;
    font-size: 41px;
    line-height: 58px;
    font-weight: 700;
    color: var(--ink);
  }
  .contact-person {
    position: absolute;
    left: 0;
    width: 1200px;
    top: 1838px;
    margin: 0;
    text-align: center;
    font-size: 41px;
    font-weight: 700;
    color: var(--brand-red);
  }
  .brand-name {
    position: absolute;
    left: 270px;
    top: 2095px;
    margin: 0;
    font-size: 45px;
    line-height: 58px;
    font-weight: 400;
    color: var(--brand-red);
    letter-spacing: 1px;
  }
  .brand-dot {
    position: absolute;
    left: 790px;
    top: 2110px;
    width: 90px;
    height: 90px;
    border-radius: 50%;
    background: var(--brand-red);
  }
  .footer-band {
    position: absolute;
    left: 0;
    bottom: 0;
    width: 1200px;
    height: 146px;
    background: var(--band-red);
  }
</style>
</head>
<body>
<main class="rack-card">
  <p class="body-copy intro">With our dedication to quality patient care, the doctors and staff of Dorwin and Partners goabove and beyond to assure your office needs are met. Wewill work with you through image interpretation, imaging follow-up, and are committed to your confidence in our process. Our goal is to help you integrate our services to create a superior diagnostic and treatment process that works for you and your practice.</p>

  <h2 class="section-title">OUR OUTPATIENT SERVICES</h2>

  <p class="body-copy services-copy">We identified a need in our communities to provide a better product for our physicians when choosing office based imaging. In 2015 we began working with Veralink Health to provide image interpretation while utilizing state of the art medical data and image management. As a physician owned practice, we pride ourselves on providing high quality and accurate reports with rapid results (a final report within 24 hours).We offer a 24 hour direct phone line for referring physicians to speak with one of our radiologists should a problem arise after hours.</p>

  <p class="callout">WE LOOK FORWARD TO BEING A<br>COMPLETE SOLUTION FOR ALL OF<br>YOUR IMAGING NEEDS.</p>

  <p class="contact">To hear more about our outpatient services<br>or free in office set up, please contact</p>
  <p class="contact-person">Dr. Marissa Hale at 517-555-0148.</p>

  <p class="brand-name">DORWIN AND<br>PARTNERS, P.C.</p>
  <div class="brand-dot" aria-hidden="true"></div>

  <div class="footer-band" aria-hidden="true"></div>
</main>
</body>
</html>
```